Business Card Design for company

We want new business cards. We'd like something different-- yet still highly professional. Our tagline is Guiding strategy, building lasting value. Stock photos are ok, as long as they are relevant and look upscale.

Target Market(s)

Architecture/Business Management Consulting/Engineering Consulting

Contact Information for Business Card

dark gray background with pops of blue might be good, but you tell me. You're the designers. Rounded corners might be nice, but again, you tell me.

Font styles to use
Serif
Sans Serif

Colors
3276b5
5c5c5c
9d9d9d
fbfbfb

Requirements
Nice to have
• Something different, but still very professional.

```html
<!DOCTYPE html>
<html lang="en">
<head>
<meta charset="utf-8">
<title>Harlow Ridge – Business Card</title>
<link rel="stylesheet" href="https://fonts.googleapis.com/css2?family=Arimo:wght@400;700&family=Jost:wght@400&display=swap">
<style>
  :root {
    --page-bg: #d9dde2;
    --panel-blue-top: #3a6598;
    --panel-blue-bottom: #1d3e6b;
    --frost-top: #fbfbfb;
    --frost-bottom: #dfe5ec;
    --brand-navy: #1f3d66;
    --text-light: #fbfbfb;
    --text-soft: #d6e0ec;
    --icon-soft: #c3cfdd;
    --tagline-bar: #3a3a3c;
    --tagline-text: #d8d8d8;
  }
  * { box-sizing: border-box; margin: 0; padding: 0; }
  html, body { width: 1200px; height: 900px; overflow: hidden; }
  body {
    background: var(--page-bg);
    font-family: "Arimo", Arial, sans-serif;
    position: relative;
  }
  .business-card {
    position: absolute;
    left: 100px; top: 165px;
    width: 1000px; height: 570px;
    display: flex;
    box-shadow: 0 14px 40px rgba(0,0,0,0.18);
  }
  .contact-panel {
    width: 435px; height: 100%;
    background: linear-gradient(160deg, var(--panel-blue-top), var(--panel-blue-bottom));
    color: var(--text-light);
    padding: 115px 0 0 46px;
  }
  .person-name { font-size: 35px; font-weight: 700; letter-spacing: 0.5px; line-height: 1; }
  .person-title { font-size: 22px; font-weight: 700; margin-top: 6px; }
  .address { font-size: 22px; line-height: 31px; margin-top: 36px; }
  .contact-list { list-style: none; margin-top: 20px; }
  .contact-list li {
    display: flex; align-items: center;
    font-size: 21px; color: var(--text-soft);
    height: 32px;
  }
  .contact-list svg { width: 22px; height: 22px; margin-right: 16px; fill: var(--icon-soft); flex: none; }
  .brand-panel {
    flex: 1; position: relative;
    background: linear-gradient(180deg, var(--frost-top), var(--frost-bottom));
  }
  .brand-name {
    position: absolute; left: 0; right: 0; top: 245px;
    text-align: center;
    font-family: "Arimo", Arial, sans-serif;
    font-weight: 700; font-size: 62px; letter-spacing: 1px;
    color: var(--brand-navy);
  }
  .tagline-bar {
    position: absolute; left: 0; right: 0; top: 483px; height: 44px;
    background: var(--tagline-bar);
    display: flex; align-items: center; justify-content: center;
    font-family: "Jost", "Futura", sans-serif;
    font-size: 22px; color: var(--tagline-text);
  }
  .tagline-dot { display: inline-block; width: 7px; height: 7px; border-radius: 50%; background: var(--tagline-text); margin: 0 8px; }
</style>
</head>
<body>
  <div class="business-card">
    <section class="contact-panel">
      <h1 class="person-name">DANIEL REYES</h1>
      <p class="person-title">CEO/FOUNDER</p>
      <p class="address">4120 Birchwood Court<br>Juniper Falls, Oregon 97410</p>
      <ul class="contact-list">
        <li>
          <svg viewBox="0 0 24 24" aria-hidden="true"><path d="M6.6 10.8a15 15 0 0 0 6.6 6.6l2.2-2.2c.3-.3.7-.4 1-.2 1.1.4 2.3.6 3.6.6.6 0 1 .4 1 1V20c0 .6-.4 1-1 1A17 17 0 0 1 3 4c0-.6.4-1 1-1h3.5c.6 0 1 .4 1 1 0 1.3.2 2.5.6 3.6.1.3 0 .7-.2 1z"/></svg>
          555 214 7830
        </li>
        <li>
          <svg viewBox="0 0 24 24" aria-hidden="true"><path d="M8 1h8a2 2 0 0 1 2 2v18a2 2 0 0 1-2 2H8a2 2 0 0 1-2-2V3a2 2 0 0 1 2-2zm0 3v14h8V4zm4 15.5a1 1 0 1 0 0 2 1 1 0 0 0 0-2z"/></svg>
          555 309 6172
        </li>
        <li>
          <svg viewBox="0 0 24 24" aria-hidden="true"><path d="M7 3h10v5H7zM4 9h16a2 2 0 0 1 2 2v7h-4v3H6v-3H2v-7a2 2 0 0 1 2-2zm4 7v3h8v-3z"/></svg>
          555 478 2056
        </li>
        <li>
          <svg viewBox="0 0 24 24" aria-hidden="true"><path d="M2 5h20v14H2zm2 2v.4l8 5.2 8-5.2V7zm0 2.8V17h16V9.8l-8 5.2z"/></svg>
          daniel@harlowridge.com
        </li>
        <li>
          <svg viewBox="0 0 24 24" aria-hidden="true"><path d="M12 2a10 10 0 1 0 0 20 10 10 0 0 0 0-20zm0 2c.9 0 2.2 2 2.7 5H9.3C9.8 6 11.1 4 12 4zM4.3 11h3a17 17 0 0 0 0 2h-3a8 8 0 0 1 0-2zm5 0h5.4a15 15 0 0 1 0 2H9.3a15 15 0 0 1 0-2zm7.4 0h3a8 8 0 0 1 0 2h-3a17 17 0 0 0 0-2zM12 20c-.9 0-2.2-2-2.7-5h5.4c-.5 3-1.8 5-2.7 5z"/></svg>
          www.harlowridge.com
        </li>
      </ul>
    </section>
    <section class="brand-panel">
      <p class="brand-name">HARLOW RIDGE</p>
      <div class="tagline-bar">Guiding strategy<span class="tagline-dot"></span>building lasting value</div>
    </section>
  </div>
</body>
</html>
```